Road Construction Company needs business cards

We would like a new business card designed for our business.

We're a road construction company based in Qld, Australia.

Can the business card please have the following information on it.

Name: Warren Halbeck
Position: General Manager
Phone: 0472 915 348
Email: Warren.halbeck@tovrin.com.au
Address: 87 Marrow Ave, Pendlebay, QLD, 4023
Website: www.tovrin.com.au

Visually we'd like the card to be professional and simple.

Attached is our logo.

Our website is www.tovrin.com.au

Target Market(s)

Men aged 25-60

Contact Information for Business Card

As listed in project description

Font styles to use
Serif

Requirements
Must have
• Large logo on back of card

```html
<!DOCTYPE html>
<html lang="en">
<head>
<meta charset="utf-8">
<title>Tovrin Road Construction – Business Card</title>
<link rel="stylesheet" href="https://fonts.googleapis.com/css2?family=Open+Sans:wght@400;600;800&display=swap">
<style>
  :root {
    --page: #e9e6e1;
    --card: #1f2025;
    --facet: #2c3238;
    --edge: #1358b0;
    --brand: #1a5cb8;
    --sky: #45a6dc;
    --white: #ffffff;
  }
  html, body {
    margin: 0;
    width: 1200px;
    height: 780px;
    overflow: hidden;
    background: var(--page);
    font-family: "Open Sans", Arial, sans-serif;
  }
  .sheet {
    width: 1200px;
    height: 780px;
    display: flex;
    align-items: center;
    justify-content: center;
    gap: 40px;
  }
  .card {
    width: 560px;
    height: 320px;
    display: block;
    filter: drop-shadow(0 8px 14px rgba(0,0,0,.25));
  }
  .card-base { fill: var(--card); stroke: var(--edge); stroke-width: 3; }
  .facet { fill: var(--facet); }
  .brand-name { fill: var(--brand); font-weight: 800; }
  .holder-name { fill: var(--sky); font-weight: 600; font-size: 24px; }
  .holder-role { fill: var(--white); font-weight: 400; font-size: 15px; }
  .contact { fill: var(--white); font-size: 13px; }
  .address { fill: var(--white); font-size: 13px; text-anchor: end; }
  .rule { stroke: var(--white); stroke-width: 1.6; }
  .band-deep { fill: var(--edge); }
  .band-sky { fill: var(--sky); }
  .icon { fill: var(--sky); }
  .icon-line { fill: none; stroke: var(--sky); stroke-width: 1.4; }
</style>
</head>
<body>
<main class="sheet">

  <svg class="card card-back" viewBox="0 0 560 320" aria-label="Business card, logo side">
    <defs>
      <clipPath id="back-clip"><rect x="1.5" y="1.5" width="557" height="317" rx="18"/></clipPath>
    </defs>
    <rect class="card-base" x="1.5" y="1.5" width="557" height="317" rx="18"/>
    <g clip-path="url(#back-clip)">
      <polygon class="facet" points="0,0 310,320 110,262 0,248"/>
    </g>
    <text class="brand-name" x="280" y="160" text-anchor="middle" font-size="66" letter-spacing="4">TOVRIN</text>
    <text class="brand-name" x="280" y="192" text-anchor="middle" font-size="15" letter-spacing="7">ROAD CONSTRUCTION</text>
  </svg>

  <svg class="card card-front" viewBox="0 0 560 320" aria-label="Business card, details side">
    <defs>
      <clipPath id="front-clip"><rect x="1.5" y="1.5" width="557" height="317" rx="18"/></clipPath>
    </defs>
    <rect class="card-base" x="1.5" y="1.5" width="557" height="317" rx="18"/>
    <g clip-path="url(#front-clip)">
      <polygon class="facet" points="430,0 520,0 560,30 560,80 505,235 475,235"/>
      <polygon class="band-deep" points="420,270 560,270 560,320 370,320"/>
      <polygon class="band-sky" points="95,304 395,292 428,292 380,320 88,320"/>
      <rect class="band-deep" x="0" y="182" width="12" height="58"/>
    </g>

    <text class="brand-name" x="36" y="78" font-size="40" letter-spacing="3">TOVRIN</text>
    <text class="brand-name" x="38" y="98" font-size="10" letter-spacing="5">ROAD CONSTRUCTION</text>

    <text class="holder-name" x="34" y="196">Warren Halbeck</text>
    <text class="holder-role" x="36" y="218">General Manager</text>
    <line class="rule" x1="170" y1="212" x2="560" y2="168"/>

    <text class="address" x="536" y="196">87 Marrow Ave,</text>
    <text class="address" x="536" y="214">Pendlebay, QLD, 4023</text>

    <g class="contact-list">
      <path class="icon" d="M74 236c-2 3 2 9 6 10l2-2-2-3-2 1c-1-1-2-3-2-4l1-1-2-3z"/>
      <text class="contact" x="92" y="246">0472 915 348</text>

      <circle class="icon-line" cx="80" cy="259" r="6"/>
      <path class="icon-line" d="M74 259h12M80 253c-3 4-3 8 0 12M80 253c3 4 3 8 0 12"/>
      <text class="contact" x="92" y="264">www.tovrin.com.au</text>

      <rect class="icon-line" x="74" y="273" width="12" height="9" rx="1"/>
      <path class="icon-line" d="M74 274l6 5 6-5"/>
      <text class="contact" x="92" y="282">Warren.halbeck@tovrin.com.au</text>
    </g>
  </svg>

</main>
</body>
</html>
```